Bottle label design for 4 litre jug

Need to create a label for my chemical products please attached label. Must have the side labels, colors must be complimented with logo attached. Come up with a clean yet high end product look to it. the brand name is Varnon Glass cleaner, Trelby Shine Works is the logo,
Redisgn with new updated look, there are a total of 8 labels to be made for oterh products.

Industry/Entity Type

Cleaning industry

Font styles to use
Serif
Other font styles liked:
• Lora Bold, EB garamond, or use any font you choose, clean and bold

Colors
0054AA
0677BA
7BADD7
CADEEF
E8F1F8
0094D4
00A9DD
6FCCEA
C7EBF8
E9F6FB
00AB8E
00BBA5
67D7C9
C6EFE9
E9F9F6

```html
<!DOCTYPE html>
<html lang="en">
<head>
<meta charset="utf-8">
<title>Varnon Glass Cleaner – 4 L Label</title>
<link rel="stylesheet" href="https://fonts.googleapis.com/css2?family=Lora:ital,wght@0,400;0,500;0,600;0,700;1,400;1,600;1,700&display=swap">
<style>
  :root {
    --navy: #0054AA;
    --ocean: #0677BA;
    --sky: #7BADD7;
    --mist: #CADEEF;
    --ice: #E8F1F8;
    --azure: #0094D4;
    --cyan: #00A9DD;
    --aqua: #6FCCEA;
    --pale-aqua: #C7EBF8;
    --foam: #E9F6FB;
    --teal: #00AB8E;
    --teal-bright: #00BBA5;
    --mint: #67D7C9;
    --pale-mint: #C6EFE9;
    --white: #ffffff;
    --ink: #0d2540;
    --hazard-red: #e01b1b;
    --page: #ffffff;
  }
  * { box-sizing: border-box; margin: 0; padding: 0; }
  html, body { width: 1200px; height: 675px; overflow: hidden; background: var(--page); }
  .canvas { position: relative; width: 1200px; height: 675px; font-family: "Lora", serif; color: var(--ink); }

  /* side panels */
  .side-panel {
    position: absolute; top: 88px; width: 232px; height: 505px;
    border: 4px solid var(--ocean); border-radius: 16px;
    background: linear-gradient(180deg, var(--foam) 0%, var(--ice) 50%, var(--pale-aqua) 100%);
    box-shadow: 0 1px 0 2px var(--aqua);
  }
  .side-panel--safety { left: 91px; padding: 7px 7px 0 8px; }
  .side-panel--directions { left: 885px; }

  .product-title { font-family: "Lora", serif; font-weight: 700; font-size: 20px; text-align: center; letter-spacing: .6px; line-height: 1; margin-bottom: 5px; color: var(--navy); }
  .hazard-copy { font-size: 7.3px; line-height: 11.2px; text-align: justify; }
  .hazard-copy b { font-weight: 700; color: var(--navy); }
  .hazard-copy--fr { font-size: 6.9px; line-height: 10.4px; }
  .sds-note { font-size: 7.2px; font-style: italic; margin: 3px 0 0; }
  .pictogram { display: block; margin: 3px auto 6px; }
  .maker { position: absolute; left: 0; right: 0; bottom: 9px; text-align: center; font-weight: 700; font-size: 11px; line-height: 14px; color: var(--navy); }

  .dir-block { position: absolute; left: 10px; right: 10px; font-size: 11.2px; line-height: 16.4px; text-align: justify; }
  .dir-block i { font-style: italic; }
  .dir-block b { font-weight: 700; color: var(--navy); }
  .freeze-note { position: absolute; left: 0; right: 0; text-align: center; font-weight: 700; font-size: 11.2px; color: var(--navy); }

  /* front panel */
  .front-panel {
    position: absolute; left: 330px; top: 86px; width: 547px; height: 508px;
    border-radius: 0 14px 14px 0; overflow: hidden;
    background: radial-gradient(ellipse 52% 48% at 52% 32%, var(--white) 0%, var(--pale-aqua) 25%, var(--aqua) 55%, var(--azure) 82%, var(--ocean) 100%);
  }
  .front-art { position: absolute; inset: 0; }
  .brand-lockup { position: absolute; left: 122px; top: 122px; width: 330px; transform: rotate(-6deg); transform-origin: left center; }
  .brand-name { display: block; font-weight: 700; font-size: 74px; line-height: 1; color: var(--navy); letter-spacing: 2px; transform: scaleY(1.3); transform-origin: left bottom; }
  .brand-sub { display: block; margin-top: 8px; font-weight: 700; font-size: 29px; line-height: 1; color: var(--white); letter-spacing: 1px; }
  .tagline { position: absolute; left: 140px; top: 297px; transform: rotate(-5deg); transform-origin: left top; font-weight: 600; font-style: italic; font-size: 11.4px; line-height: 14px; color: var(--navy); text-align: center; }
  .volume-text { position: absolute; left: 30px; top: 430px; font-weight: 700; font-size: 29px; color: var(--white); letter-spacing: 2px; }
  .claims { position: absolute; right: 46px; top: 404px; text-align: right; font-weight: 600; font-size: 18.5px; line-height: 24.6px; color: var(--white); }
</style>
</head>
<body>
<div class="canvas">

  <section class="side-panel side-panel--safety">
    <h2 class="product-title">GLASS CLEAN</h2>
    <p class="hazard-copy"><b>WARNING: Causes eye irritation. Prolonged or repeated skin contact may cause irritation.</b><br>
    <b>PRECAUTIONS:</b> Wash hands thoroughly after handling. Wear protective gloves/eye protection/face protection. Do not eat, drink, or smoke when using this product.<br>
    <b>FIRST AID:</b> IF IN EYES: Rinse cautiously with water for several minutes. Remove contact lenses, if present and easy to do. Continue rinsing. If eye irritation persists: get medical attention/advice. IF SWALLOWED: Rinse mouth. DO NOT induce vomiting. Drink large quantities of water. Call a POISON CENTER or doctor/physician if you feel unwell. If skin irritation occurs: Get medical advice/attention.</p>
    <p class="sds-note">See Safety Data Sheet.</p>
    <svg class="pictogram" width="64" height="64" viewBox="0 0 66 66" aria-label="Exclamation hazard pictogram">
      <rect x="13" y="13" width="40" height="40" transform="rotate(45 33 33)" fill="#fff" stroke="var(--hazard-red)" stroke-width="3.5"/>
      <rect x="30" y="15" width="6" height="25" rx="3" fill="#111"/>
      <circle cx="33" cy="46.5" r="3.6" fill="#111"/>
    </svg>
    <p class="hazard-copy hazard-copy--fr"><b>ATTENTION: Provoque une irritation oculaire. Un contact cutané prolongé ou répété peut provoquer une irritation.</b><br>
    <b>PRÉCAUTIONS:</b> Se laver soigneusement après la manipulation. Porter des gants de protection/protection des yeux/protection du visage. Ne pas manger, boire ou fumer lors de l'utilisation de ce produit.<br>
    <b>PREMIER SOINS:</b> EN CAS DE CONTACT AVEC LES YEUX: Rincer avec précaution à l'eau pendant plusieurs minutes. Enlevez les lentilles de contact si la victime en porte et si elles peuvent être facilement enlevées. Continuer à rinçage. Si l'irritation des yeux persiste: consulter un médecin. EN CAS D'INGESTION: Rincer la bouche. NE PAS faire vomir. Buvez de grandes quantités d'eau. Appelez un CENTRE ANTIPOISON/un médecin en cas de malaise. En cas d'irritation cutanée: Consulter un médecin.</p>
    <p class="sds-note">Consulter la fiche de données de securité.</p>
    <p class="maker">TRELBY SHINE WORKS<br>Harrowfield, Ontario K9X 2T4</p>
  </section>

  <section class="front-panel">
    <svg class="front-art" width="547" height="508" viewBox="0 0 547 508">
      <defs>
        <linearGradient id="lowerBand" x1="0" y1="0" x2="1" y2="1">
          <stop offset="0" stop-color="#67D7C9"/>
          <stop offset=".5" stop-color="#00BBA5"/>
          <stop offset="1" stop-color="#00AB8E"/>
        </linearGradient>
        <linearGradient id="swoosh" x1="0" y1="0" x2="1" y2="0">
          <stop offset="0" stop-color="#7BADD7"/>
          <stop offset=".5" stop-color="#ffffff"/>
          <stop offset="1" stop-color="#E8F1F8"/>
        </linearGradient>
      </defs>
      <path d="M0 400 C 170 360, 380 350, 547 312 L547 508 L0 508 Z" fill="url(#swoosh)"/>
      <path d="M0 410 C 170 372, 380 362, 547 320 L547 508 L0 508 Z" fill="url(#lowerBand)"/>
      <circle cx="44" cy="32" r="98" fill="var(--navy)" role="img" aria-label="Eco certification badge"/>
      <path d="M0 424 H113 L98 448.5 L113 473 H0 Z" fill="var(--navy)"/>
    </svg>
    <div class="brand-lockup">
      <span class="brand-name">VARNON</span>
      <span class="brand-sub">GLASS CLEANER</span>
    </div>
    <p class="tagline">Dries fast without leaving a flim or streaking.<br>Polishes as it dissolves dirt and dingy flim.</p>
    <span class="volume-text">4 L</span>
    <p class="claims">Non Corrosive<br>Low Carbon Footprint<br>Completely Biodegradeable</p>
  </section>

  <section class="side-panel side-panel--directions">
    <p class="dir-block" style="top:10px"><i>Read entire label before using. For industrial and institutional use only.</i> <b>Keep out of reach of children.</b></p>
    <p class="dir-block" style="top:112px"><i>For windows, glass, mirrors, windshields, ceramic tile, porcelain, etc.</i> Use full strength. Spray on and wipe off with a clean towel or cloth.</p>
    <p class="freeze-note" style="top:200px">NOT AFFECTED BY FREEZING.</p>
    <p class="dir-block" style="top:258px"><i>Lire l’etiquette au complet avant d’utiliser le produit. Pour usage industrial ou dans un establissement seulement.</i> <b>Garder hors de la portée des enfants.</b></p>
    <p class="dir-block" style="top:398px"><i>Pour vitres, miroirs, carreaux en céramique, verre, porcelaine, etc.</i> Ne pas diluer. Vaporiser et essuyer à laide d’un chiffon propre.</p>
    <p class="freeze-note" style="top:479px">NE CRAINT PAS LE GEL.</p>
  </section>

</div>
</body>
</html>
```